Postcard designed to acquire new customers

Need a postcard style AD to place in dentist offices and other professionals to promote our tax saving system. We will place these in dentists offices, orthodontist, optometrist, physiotherapist and all sorts of medical/dental offices. The card should highlight how they can save taxes by using our software. Our website has good information on it, and I'll include the advertising PDF that our software company produces. Our logo is a little out-dated and I've included the bonus of the winner re-making the logo so its better than it currently is.
Updates

I don't need to have any space allocated for a stamp and address. We are using this to place in offices and are for advertising purposes, not mailing. Thanks!

Reason: My apologies for not providing feedback yet, I've lost several days due to some illness and am finally back at work. I'll be going through designs today and would like the extra few days to work with many of you to create a great design. Thank you for your patience! Dorian

Reason: Again, my apologies for the delay. I will be in contact with designers this week. Thank you,

Target Market(s)

Small Business Owners in Canada

Industry/Entity Type

Health Insurance

Logo Text

Save Time, Save Money

Font styles to use
Other font styles liked:
• Easy to Read Font's

Colors

Designer to choose colors to be used in the design.

Requirements
Must have
• Must have a call to action on the postcard to sell the service. We need people to have their attention caught. A call to action could be, "You're spending too much on taxes! That's what they'll say if your business doesn't have a Birchline Health Spending Account..."
• See the PDF for other catch phrases or key information on what a Health Spending Account is. Many people don't know so I'd like to see 3-4 bullet points on the front of the postcard on what a health spending account is. See the attached PDF for that information and simplifying the information to short bullet points would be best. Here are my thoughts:
• Who should have a Birchline Health Spending Account?
• - Every business owner who is incorporated should have one.
• - Write off 100% of this NFB approved this method.
• - It is the most tax effective way to run dental, health, vision and other expenses through your company.
• - Easy to use APP for your phone, 2-day turnaround time for claims
• If you aren't using this, you're throwing tax dollars away!
• The back of the postcard would include 2 things. First, an example of the taxes you can save, and second - the different information they can send us so we can setup your account.
• First is the example of how this saves you money. Assuming a 38% personal tax rate. You will need to earn $1.62 of gross income, pay $0.62 of personal tax, which leaves you with $1.00 of after tax money to use for your personal expenses.
• The example of using a Birchline Health Spending Account, or doing nothing would need the following information.
• Comparison
• $5,000 of medical, dental, vision expenses
• Do Nothing Birchline Health Spending Account
• $8,100 – Total Cost $5,525 – Total Cost
• $3,100 – Income Tax $500 fee & $25 GST
• $5,000 – Money needed for medical, dental, vision, etc. $5,000 – Money needed for medical, dental, vision, etc.
• SAVINGS is $2,575
• Assuming a company incorporated in Alberta and a one time setup fee of $275 has not been included in the comparison.
• Information to send us to setup your account is:
• - Names and birth dates of you and your dependents
• - Contact information for you and your business (if different) Address, email, phone numbers
• - We will contact you about how to setup the app, your banking details and some other items.
• - Setup fee is a one-time payment of $275
Nice to have
• I'd like the front of the postcard to not be very busy with the background or graphics, etc. I want the call to action to be very obvious so they want to read the bullet points and look at the back of the postcard for more information.

```html
<!DOCTYPE html>
<html lang="en">
<head>
<meta charset="utf-8">
<title>Birchline Health Spending Postcard</title>
<link href="https://fonts.googleapis.com/css2?family=Roboto+Condensed:wght@400;700&display=swap" rel="stylesheet">
<style>
  :root {
    --page-bg: #5a5a5c;
    --brand-blue: #2e3192;
    --divider-grey: #8a8c8f;
    --ink: #1d1d1f;
    --tagline-grey: #4a4a4a;
    --badge-black: #0d0d0d;
    --white: #ffffff;
  }
  * { margin: 0; padding: 0; box-sizing: border-box; }
  html, body {
    width: 1200px; height: 800px; overflow: hidden;
    background: var(--page-bg);
    font-family: "Roboto Condensed", "Arial Narrow", sans-serif;
  }
  .postcard {
    position: absolute; left: 59px; top: 53px;
    width: 1081px; height: 695px;
    background: #dfe3ee; overflow: hidden;
  }
  .header-band {
    position: absolute; left: 0; top: 0; width: 100%; height: 148px;
    background: var(--brand-blue); color: var(--white);
    display: flex; flex-direction: column; justify-content: center; align-items: center;
    font-weight: 700; font-size: 48px; line-height: 57px; text-align: center;
  }
  .header-rule {
    position: absolute; left: 0; top: 148px; width: 100%; height: 10px;
    background: var(--divider-grey);
  }
  .hero-photo {
    position: absolute; left: 0; top: 158px; width: 100%; height: 523px;
    background:
      radial-gradient(ellipse 420px 300px at 380px 260px, rgba(231,196,170,0.55), transparent 70%),
      radial-gradient(ellipse 300px 260px at 900px 260px, rgba(226,190,165,0.7), transparent 70%),
      linear-gradient(100deg, #e6e8f1 0%, #d9dcea 45%, #c9d0e6 100%);
  }
  .hero-photo::after {
    content: ""; position: absolute; inset: 0;
    background: linear-gradient(90deg, rgba(255,255,255,0.55) 0%, rgba(255,255,255,0.35) 60%, rgba(255,255,255,0) 100%);
  }
  .savings-illustration {
    position: absolute; left: 741px; top: 195px; width: 330px; height: 300px;
    background:
      radial-gradient(circle at 70px 100px, rgba(214,168,48,0.85), transparent 40%),
      radial-gradient(circle at 260px 200px, rgba(233,150,160,0.6), transparent 30%),
      radial-gradient(circle at 170px 250px, rgba(140,140,145,0.55), transparent 30%);
  }
  .footer-band {
    position: absolute; left: 0; bottom: 0; width: 100%; height: 14px;
    background: var(--brand-blue);
  }
  .pitch { position: absolute; left: 30px; top: 196px; }
  .pitch-line { font-size: 42px; line-height: 51px; color: var(--ink); white-space: nowrap; }
  .pitch-line.emphasis { font-weight: 700; color: var(--brand-blue); }
  .benefits {
    position: absolute; left: 30px; top: 420px;
    list-style: none; font-size: 21px; line-height: 26px; color: var(--ink);
  }
  .benefits li { position: relative; padding-left: 27px; margin-bottom: 10px; white-space: nowrap; }
  .benefits li::before {
    content: ""; position: absolute; left: 2px; top: 9px;
    width: 9px; height: 9px; background: var(--brand-blue);
    transform: rotate(45deg); border-radius: 2px;
  }
  .brand-lockup {
    position: absolute; left: 712px; top: 539px; width: 366px; text-align: center;
  }
  .brand-name {
    display: flex; align-items: center; justify-content: center; gap: 10px;
    font-weight: 700; font-size: 40px; line-height: 40px; color: var(--ink);
  }
  .brand-mark {
    width: 26px; height: 26px; border-radius: 50%; background: var(--brand-blue); flex: none;
  }
  .brand-tagline {
    margin-top: 2px; font-weight: 700; font-size: 21px; line-height: 25px;
    color: var(--tagline-grey); letter-spacing: 0.5px;
  }
  .store-badge {
    position: absolute; top: 619px; height: 40px;
    background: var(--badge-black); border: 1px solid #b5b5b5; border-radius: 5px;
  }
  .store-badge.first { left: 751px; width: 144px; }
  .store-badge.second { left: 901px; width: 120px; }
</style>
</head>
<body>
  <main class="postcard">
    <header class="header-band">
      <span>Now You Can Save Taxes By</span>
      <span>Using Our Software</span>
    </header>
    <div class="header-rule"></div>

    <div class="hero-photo" role="img" aria-label="Photo of hands holding a smartphone, softly faded"></div>
    <div class="savings-illustration" role="img" aria-label="Illustration of a gold dollar sign, a calculator and a pink piggy bank on coins"></div>

    <section class="pitch">
      <p class="pitch-line emphasis">You're spending too much on taxes!</p>
      <p class="pitch-line">That's what they'll say if your business</p>
      <p class="pitch-line">doesn't have a</p>
      <p class="pitch-line emphasis">Birchline Health Spending Account...</p>
    </section>

    <ul class="benefits">
      <li>Who should have a Birchline Health Spending Account?</li>
      <li>Every business owner who is incorporated should have one.</li>
      <li>Write off 100% of this NFB approved this method.</li>
      <li>It is the most tax effective way to run dental, health, vision and<br>other expenses through your company.</li>
      <li>Easy to use APP for your phone, 2-day turnaround time for claims</li>
      <li>If you aren't using this, you're throwing tax dollars away!</li>
    </ul>

    <div class="brand-lockup">
      <div class="brand-name"><span class="brand-mark"></span><span>BIRCHLINE HEALTH</span></div>
      <div class="brand-tagline">SAVE TIME - SAVE MONEY</div>
    </div>

    <div class="store-badge first" role="img" aria-label="Mobile app download badge"></div>
    <div class="store-badge second" role="img" aria-label="Second mobile app download badge"></div>

    <div class="footer-band"></div>
  </main>
</body>
</html>
```